QVR business card

Need a business card for a company that provides instructional design and elearning development services. The website is here: http://quorvane.studio/

I'm attaching a current logo, as well as the old business card design. While I like to keep it clean, the old design is too simplistic for my liking. The only idea I want to reuse from the old design is placing industry jargon on the back of the card, just need a better way to present it. But if you have other ideas for the back--feel free to experiment.

Please use the colors complementary to the color we have on the website. Thank you!

```html
<!DOCTYPE html>
<html lang="en">
<head>
<meta charset="utf-8">
<title>QVR Business Card</title>
<link href="https://fonts.googleapis.com/css2?family=Open+Sans:wght@400;600;700&display=swap" rel="stylesheet">
<style>
  :root {
    --teal: #12b3ad;
    --teal-dark: #0fa39e;
    --sand: #e4d89c;
    --ink: #1f1f1f;
    --white: #ffffff;
    --stage: #eef0ef;
    --icon-green: #5cb85c;
  }
  * { box-sizing: border-box; margin: 0; padding: 0; }
  html, body {
    width: 1200px; height: 900px; overflow: hidden;
    background: var(--stage);
    font-family: "Open Sans", Arial, sans-serif;
  }
  .canvas { position: relative; width: 1200px; height: 900px; }
  .card {
    position: absolute; width: 580px; height: 330px; border-radius: 4px;
    box-shadow: 0 10px 28px rgba(0,0,0,.14);
    overflow: hidden;
  }
  .card-back {
    left: 80px; top: 110px;
    background: linear-gradient(180deg, var(--teal) 0%, #4fc0ae 45%, var(--sand) 100%);
    color: var(--white);
  }
  .card-front { left: 540px; top: 470px; background: var(--white); }

  .services { position: absolute; left: 318px; top: 34px; }
  .services-title { font-size: 17px; font-weight: 700; letter-spacing: .5px; margin-bottom: 10px; }
  .services-list { list-style: none; padding-left: 14px; }
  .services-list li {
    font-size: 13px; font-weight: 600; line-height: 21px;
    display: flex; align-items: center; gap: 10px;
  }
  .services-list li::before {
    content: ""; width: 7px; height: 7px; border-radius: 50%; background: var(--white);
  }

  .brand { position: absolute; display: flex; align-items: center; gap: 12px; font-weight: 700; }
  .brand-back { left: 44px; bottom: 40px; font-size: 58px; color: var(--white); }
  .brand-front { left: 48px; bottom: 46px; font-size: 58px; color: var(--teal); }
  .brand-dot { width: 40px; height: 40px; border-radius: 50%; background: var(--teal); }
  .brand-back .brand-dot { background: var(--white); }

  .contact { position: absolute; left: 312px; top: 42px; }
  .contact-name { font-size: 17px; font-weight: 700; color: var(--teal); margin-bottom: 12px; }
  .contact-list { list-style: none; }
  .contact-list li {
    font-size: 12.5px; color: var(--ink); line-height: 19px;
    display: flex; align-items: center; gap: 8px;
  }
  .contact-list svg { width: 11px; height: 11px; flex: none; }
</style>
</head>
<body>
<main class="canvas">
  <section class="card card-back" aria-label="Card back">
    <div class="services">
      <h2 class="services-title">HOW CAN WE HELP?</h2>
      <ul class="services-list">
        <li>Mobile Learning Scorm</li>
        <li>Instructional Design Lms</li>
        <li>Moocs Elearning Html5</li>
        <li>Adult Learning Theory</li>
        <li>Gamification Classroom</li>
        <li>Xapi Blended Learning</li>
      </ul>
    </div>
    <div class="brand brand-back"><span class="brand-dot"></span>QVR</div>
  </section>

  <section class="card card-front" aria-label="Card front">
    <div class="contact">
      <h1 class="contact-name">Darian Holloway</h1>
      <ul class="contact-list">
        <li>
          <svg viewBox="0 0 12 12"><path d="M3 1l2 2.5-1.2 1.3a7 7 0 0 0 3.4 3.4L8.5 7 11 9l-1 2C5 11 1 7 1 2z" fill="var(--teal)"/></svg>
          555-014-2780
        </li>
        <li>
          <svg viewBox="0 0 12 12"><rect x="1" y="2.5" width="10" height="7" fill="var(--icon-green)"/><path d="M1 2.5l5 4 5-4" stroke="#fff" fill="none"/></svg>
          dholloway@quorvane.studio
        </li>
        <li>
          <svg viewBox="0 0 12 12"><circle cx="6" cy="6" r="5" fill="var(--teal)"/><path d="M1 6h10M6 1c-2.5 3-2.5 7 0 10M6 1c2.5 3 2.5 7 0 10" stroke="#fff" stroke-width=".8" fill="none"/></svg>
          www.quorvane.studio
        </li>
      </ul>
    </div>
    <div class="brand brand-front"><span class="brand-dot"></span>QVR</div>
  </section>
</main>
</body>
</html>
```